Webdesign for a business that converts shops into apps. UPDATE BRIEF

We want a creative/professional design for our new business Vorbo.

Vorbo is a service that can deliver instant apps for quillora shops. So every shop owner can have its own app for selling to there customers.

We are open for your interpretation of the design. We think it could be intersting doing an onepage design for this. But thats not set in stones offcourse.

We need several section:
top section
some facts abt the service and maybe our company
price table
some customer review
functionalitys of the app (in a nice way shown)
Section showing screens of a demo shop.
footer with ccdetails, socialmedia, newsletter

I have been playing abit myself with a theme, but no development/designer experience. And we really need a very professional and custom look.

Ps. we are an ecommerce company so if we find any good designer here, we will have enough work for you.

Some competitors in this field;

http://shrt.example/k7Tq2Zw
http://shrt.example/p3Nx9Ld

Here is a design we like
http://brelunoweb.example/

Hoping for some great concepts!

Kind Regards and good luck!

Some screenshots which can be used for app demo;

UPDATE BRIEF

We would like to add a section for features of the app.
We would like to show a zelphone screen and all the most important features of the app and when clicking every feature the screen would change or the feature intened would be high lighted in some way.

The features and any content and info abt that can be used from
https://www.tovexa.example/features.html/

We need an how it works section aswell in the design, also that can be used content from here
https://www.tovexa.example/how-it-works/

Tovexa is our partner, so there work way and features are same as ours. We just want it in a different 'look and feel/design)

Reason: Getting very few good design at the moment. Same designers seem to be responding whith 5 designs at a time of low quality.

Target Market(s)

quillora webshop

Industry/Entity Type

Business

Number of Pages Required

1 page

Font styles to use
Sans Serif

Colors
0355a3
3176b5
85acd3
85cae6
33a6d7
0392cd
f59195
33b8a4

Requirements
Must have
• a creative and custom look, not a copied theme vibe.
Nice to have
• it would be nice if the entire design has a nice flow goinf through the site. The customers experience should be on point.
Should not have
• boring static experience

```html
<!DOCTYPE html>
<html lang="en">
<head>
<meta charset="utf-8">
<title>Vorbo – Grow your business with a mobile app</title>
<link rel="stylesheet" href="https://fonts.googleapis.com/css2?family=Baumans&family=Open+Sans:wght@400;600;700&display=swap">
<style>
:root{
  --navy:#0355a3;
  --blue:#3176b5;
  --sky:#33a6d7;
  --ink:#333333;
  --muted:#8a8a8a;
  --row:#f1f1f1;
  --light:#f7f7f7;
  --red:#e8484f;
  --white:#ffffff;
  --handset:#2a2a2a;
}
*{margin:0;padding:0;box-sizing:border-box}
html,body{width:1200px;height:3579px;overflow:hidden}
body{position:relative;background:var(--white);font-family:"Open Sans",Arial,sans-serif;color:var(--ink)}
.abs{position:absolute}
section,header,footer{position:absolute;left:0;width:1200px}
.display{font-family:"Baumans","Open Sans",sans-serif;font-weight:400}

/* header */
.site-header{top:0;height:79px;background:var(--white)}
.brand{left:86px;top:16px;font-size:34px;font-weight:700;color:var(--navy);letter-spacing:-0.5px}
.main-nav a{position:absolute;white-space:nowrap;font-size:13px;font-weight:700;color:var(--navy);text-decoration:none}
.login-btn{left:995px;top:22px;width:118px;height:34px;border:1.5px solid var(--red);border-radius:3px;color:var(--red);font-size:15px;display:flex;align-items:center;justify-content:center;gap:8px}

/* hero */
.hero{top:79px;height:477px;background:linear-gradient(135deg,#4a8bc9 0%,#3a7bbd 55%,#2f6fb3 100%)}
.hero-visual{left:100px;top:30px;width:360px;height:447px;border-radius:40px 40px 0 0;
  background:radial-gradient(ellipse 55% 60% at 55% 40%,rgba(255,255,255,.95) 0%,rgba(235,224,214,.85) 45%,rgba(214,186,164,.55) 70%,rgba(74,139,201,0) 100%)}
.hero-title{right:86px;top:148px;text-align:right;color:var(--white);font-size:44px;line-height:58px;letter-spacing:.5px;white-space:nowrap}
.hero-btn{left:967px;top:277px;width:147px;height:38px;border:1.5px solid var(--white);border-radius:3px;color:var(--white);font-family:"Baumans",sans-serif;font-size:14px;display:flex;align-items:center;justify-content:center;gap:6px}
.slider-arrow{width:42px;height:42px;border-radius:50%;background:var(--white);display:flex;align-items:center;justify-content:center}

/* section titles */
.section-title{width:1200px;text-align:center;font-size:24px;color:#222}
.section-sub{width:1200px;text-align:center;font-size:13px;color:#555}

/* services */
.services{top:556px;height:716px;background:var(--light)}
.feature{width:330px;height:90px}
.feature .icon{position:absolute;left:0;top:0;width:50px;height:50px;border:1.5px solid #d4d4d4;border-radius:50%;display:flex;align-items:center;justify-content:center;background:var(--white)}
.feature h3{position:absolute;left:76px;top:0;font-size:15px;font-weight:700;color:#333}
.feature p{position:absolute;left:76px;top:27px;width:260px;font-size:12px;line-height:19px;color:var(--muted)}
.device{left:496px;top:188px;width:208px;height:430px;border-radius:34px;
  background:radial-gradient(ellipse 60% 45% at 50% 48%,#8a7a6c 0%,#b9b2ab 45%,#e6e6e6 75%,#f1f1f1 100%);
  box-shadow:0 8px 24px rgba(0,0,0,.12)}

/* pricing */
.pricing{top:1272px;height:780px;background:var(--white)}
.plan{top:195px;width:317px;height:518px;background:var(--white)}
.plan.featured{box-shadow:0 2px 16px rgba(0,0,0,.18)}
.plan-head{left:0;top:0}
.plan-name{left:0;top:30px;width:317px;text-align:center;color:var(--white);font-size:13px;font-weight:700}
.plan-price{left:108px;top:65px;width:100px;height:100px;border-radius:50%;background:var(--white);border:3px solid var(--sky);display:flex;align-items:center;justify-content:center;font-size:27px;font-weight:700;color:#222}
.plan-price small{font-size:15px;font-weight:700;margin-top:8px}
.plan-rows{left:0;top:215px;width:317px;list-style:none}
.plan-rows li{height:36px;display:flex;align-items:center;justify-content:center;font-size:12px;color:#666}
.plan-rows li:nth-child(odd){background:var(--row)}
.plan-rows li.off{text-decoration:line-through}
.plan-btn{left:67px;top:420px;width:183px;height:46px;background:var(--sky);color:var(--white);font-size:12px;font-weight:700;display:flex;align-items:center;justify-content:center}
.plan-foot{left:0;bottom:0;width:317px;height:17px;background:var(--sky)}

/* reviews */
.reviews{top:2052px;height:437px;background:linear-gradient(135deg,#6dcfcf 0%,#55c1c3 50%,#47b6b8 100%)}
.reviews .section-title{color:#1f2f3a}
.review-text{left:390px;top:100px;width:420px;text-align:center;font-size:13px;line-height:20px;color:var(--white)}
.review-name{top:350px;width:1200px;text-align:center;font-size:13px;font-weight:700;color:var(--white)}
.review-role{top:372px;width:1200px;text-align:center;font-size:10px;color:#e8f8f8}

/* screenshots */
.screens{top:2489px;height:546px;background:var(--white)}
.handset{border-radius:18px;background:var(--handset);box-shadow:0 6px 14px rgba(0,0,0,.25)}
.handset .screen{position:absolute;left:8%;top:11%;width:84%;height:72%;
  background:linear-gradient(180deg,#f2a25a 0%,#f4efe9 14%,#dcd7d2 50%,#c9c1b8 80%,#eeeeee 100%)}

/* download */
.download{top:3035px;height:305px;background:linear-gradient(135deg,#5a9bd1 0%,#3f86c6 50%,#3479bd 100%)}
.download .section-title{color:var(--white);top:80px;font-size:24px}
.download .section-sub{color:var(--white);top:118px}
.store-btn{top:177px;height:52px;background:var(--white);border-radius:3px;display:flex;align-items:center;gap:14px;padding-left:16px}
.store-btn .mark{width:22px;height:22px;background:#c9c9c9;border-radius:2px}
.store-btn span{font-size:11px;color:#666;line-height:15px}
.store-btn b{display:block;font-size:14px;font-weight:600;color:#333}

/* footer */
.site-footer{top:3340px;height:239px;background:var(--white)}
.footer-brand{left:86px;top:36px;font-size:34px;font-weight:700;color:var(--navy)}
.contact-line{left:86px;display:flex;align-items:center;gap:12px;font-size:14px;color:#333}
.copyright{left:86px;top:190px;font-size:11px;color:#555}
.pay-badge{left:401px;top:50px;width:184px;height:52px;border:2px solid #1c3f8f;border-radius:4px;background:#eef2f8}
.social{top:136px;width:22px;height:22px;background:var(--navy);border-radius:3px}
.news-title{left:759px;top:40px;font-size:24px;color:#222}
.news-note{left:759px;top:90px;font-size:11px;color:var(--red)}
.news-form{left:759px;top:116px;width:353px;height:42px;border:1px solid #9fc2de;border-radius:3px;display:flex}
.news-form .field{flex:1;font-size:11px;color:#999;padding:0 14px;display:flex;align-items:center}
.news-form .submit{width:86px;background:var(--navy);color:var(--white);font-size:11px;font-weight:700;display:flex;align-items:center;justify-content:center}
</style>
</head>
<body>

<header class="site-header">
  <div class="abs brand">Vorbo</div>
  <nav class="abs main-nav" style="left:0;top:31px;width:1200px">
    <a style="left:327px">HOME</a>
    <a style="left:413px">ABOUT</a>
    <a style="left:510px">SERVICES &nbsp;<svg width="9" height="6" viewBox="0 0 9 6"><path d="M1 1l3.5 3.5L8 1" fill="none" stroke="#0355a3" stroke-width="1.4"/></svg></a>
    <a style="left:640px">PRICING</a>
    <a style="left:725px">TESTIMONIALS</a>
    <a style="left:872px">CONTACT</a>
  </nav>
  <div class="abs login-btn">
    <svg width="12" height="14" viewBox="0 0 12 14"><rect x="1" y="6" width="10" height="7.5" rx="1" fill="#e8484f"/><path d="M3 6V4a3 3 0 0 1 6 0v2" fill="none" stroke="#e8484f" stroke-width="1.6"/></svg>
    log in
  </div>
</header>

<section class="hero">
  <div class="abs hero-visual" role="img" aria-label="Hand holding a white smartphone showing the Vorbo app start screen"></div>
  <h1 class="abs hero-title display">Grow your business brilliantly<br>with Vorbo mobile app!</h1>
  <div class="abs hero-btn">
    <svg width="11" height="11" viewBox="0 0 11 11"><path d="M5.5 1v6M2.5 4.5l3 3 3-3M1 10h9" fill="none" stroke="#fff" stroke-width="1.5"/></svg>
    download now
  </div>
  <div class="abs slider-arrow" style="left:25px;top:215px"><svg width="14" height="16" viewBox="0 0 14 16"><path d="M10 2L4 8l6 6" fill="none" stroke="#2f6fb3" stroke-width="3"/></svg></div>
  <div class="abs slider-arrow" style="left:1133px;top:215px"><svg width="14" height="16" viewBox="0 0 14 16"><path d="M4 2l6 6-6 6" fill="none" stroke="#2f6fb3" stroke-width="3"/></svg></div>
</section>

<section class="services">
  <h2 class="abs section-title display" style="top:76px;font-size:26px">SERVICES</h2>
  <p class="abs section-sub" style="top:122px">Lorem ipsum dolor sit a met, consectetur adipiscing elit, sed do eiusmod tempor</p>

  <div class="abs feature" style="left:89px;top:216px">
    <div class="icon"><svg width="22" height="18" viewBox="0 0 22 18"><rect x="1" y="4" width="20" height="13" rx="2" fill="none" stroke="#0355a3" stroke-width="1.8"/><circle cx="11" cy="10.5" r="3.5" fill="none" stroke="#0355a3" stroke-width="1.8"/><rect x="7" y="1" width="8" height="3" fill="#0355a3"/></svg></div>
    <h3>Smart camera</h3>
    <p>Lorem ipsum dolor sit amet, consectetur adipiscing elit, sed do eiusmod tempor incididunt ut labore.</p>
  </div>
  <div class="abs feature" style="left:89px;top:320px">
    <div class="icon"><svg width="24" height="18" viewBox="0 0 24 18"><path d="M6 16a5 5 0 0 1 0-10 7 7 0 0 1 13 2 4 4 0 0 1 0 8z" fill="#0355a3"/><path d="M12 7v6M9.5 10.5L12 13l2.5-2.5" fill="none" stroke="#fff" stroke-width="1.6"/></svg></div>
    <h3>Download mannager</h3>
    <p>Lorem ipsum dolor sit amet, consectetur adipiscing elit, sed do eiusmod tempor incididunt ut labore.</p>
  </div>
  <div class="abs feature" style="left:89px;top:424px">
    <div class="icon"><svg width="20" height="20" viewBox="0 0 20 20"><circle cx="15" cy="4" r="3" fill="#0355a3"/><circle cx="5" cy="10" r="3" fill="#0355a3"/><circle cx="15" cy="16" r="3" fill="#0355a3"/><path d="M15 4L5 10l10 6" fill="none" stroke="#0355a3" stroke-width="1.6"/></svg></div>
    <h3>Photo sharing</h3>
    <p>Lorem ipsum dolor sit amet, consectetur adipiscing elit, sed do eiusmod tempor incididunt ut labore.</p>
  </div>
  <div class="abs feature" style="left:89px;top:528px">
    <div class="icon"><svg width="16" height="22" viewBox="0 0 16 22"><rect x="4.5" y="1" width="7" height="12" rx="3.5" fill="#0355a3"/><path d="M1.5 10a6.5 6.5 0 0 0 13 0M8 16.5V21M4.5 21h7" fill="none" stroke="#0355a3" stroke-width="1.6"/></svg></div>
    <h3>Voice maker</h3>
    <p>Lorem ipsum dolor sit amet, consectetur adipiscing elit, sed do eiusmod tempor incididunt ut labore.</p>
  </div>

  <div class="abs device" role="img" aria-label="White smartphone showing a demo shop home screen with product photos"></div>

  <div class="abs feature" style="left:755px;top:216px">
    <div class="icon"><svg width="14" height="22" viewBox="0 0 14 22"><rect x="1" y="1" width="12" height="20" rx="2" fill="none" stroke="#0355a3" stroke-width="1.8"/><circle cx="7" cy="17.5" r="1.2" fill="#0355a3"/></svg></div>
    <h3>User friendly</h3>
    <p>Lorem ipsum dolor sit amet, consectetur adipiscing elit, sed do eiusmod tempor incididunt ut labore.</p>
  </div>
  <div class="abs feature" style="left:755px;top:320px">
    <div class="icon"><svg width="20" height="20" viewBox="0 0 20 20"><circle cx="10" cy="10" r="6" fill="none" stroke="#0355a3" stroke-width="4" stroke-dasharray="3 2.3"/><circle cx="10" cy="10" r="4.5" fill="#0355a3"/><circle cx="10" cy="10" r="2" fill="#fff"/></svg></div>
    <h3>Easy to customize</h3>
    <p>Lorem ipsum dolor sit amet, consectetur adipiscing elit, sed do eiusmod tempor incididunt ut labore.</p>
  </div>
  <div class="abs feature" style="left:755px;top:424px">
    <div class="icon"><svg width="16" height="22" viewBox="0 0 16 22"><path d="M8 1a6.5 6.5 0 0 0-3.5 12v3h7v-3A6.5 6.5 0 0 0 8 1z" fill="none" stroke="#0355a3" stroke-width="1.7"/><path d="M5 18.5h6M6 21h4" stroke="#0355a3" stroke-width="1.7"/></svg></div>
    <h3>Creative design</h3>
    <p>Lorem ipsum dolor sit amet, consectetur adipiscing elit, sed do eiusmod tempor incididunt ut labore.</p>
  </div>
  <div class="abs feature" style="left:755px;top:528px">
    <div class="icon"><svg width="22" height="20" viewBox="0 0 22 20"><circle cx="11" cy="9" r="6" fill="none" stroke="#0355a3" stroke-width="1.7"/><circle cx="11" cy="9" r="2" fill="#0355a3"/><path d="M3 17c2-2 14-2 16 0" fill="none" stroke="#0355a3" stroke-width="1.7"/></svg></div>
    <h3>New look</h3>
    <p>Lorem ipsum dolor sit amet, consectetur adipiscing elit, sed do eiusmod tempor incididunt ut labore.</p>
  </div>
</section>

<section class="pricing">
  <h2 class="abs section-title" style="top:56px;font-weight:700;font-size:24px">PRICING PLAN</h2>
  <p class="abs section-sub" style="top:99px">Lorem ipsum dolor sit a met, consectetur adipiscing elit, sed do eiusmod tempor</p>

  <div class="abs plan" style="left:88px">
    <svg class="abs plan-head" width="317" height="170" viewBox="0 0 317 170"><polygon points="0,0 317,0 317,82 158.5,150 0,82" fill="#33a6d7"/></svg>
    <div class="abs plan-name">BASIC PLAN</div>
    <div class="abs plan-price">$49<small>.00</small></div>
    <ul class="abs plan-rows"><li>Responsive</li><li class="off">1.5 GB of storage</li><li>Battery backup 10%</li><li class="off">Smart wallpaper</li><li>50 Feature</li></ul>
    <div class="abs plan-btn">SIGNUP NOW</div>
    <div class="abs plan-foot"></div>
  </div>

  <div class="abs plan featured" style="left:439px">
    <svg class="abs plan-head" width="317" height="170" viewBox="0 0 317 170"><polygon points="0,0 317,0 317,82 158.5,150 0,82" fill="#33a6d7"/></svg>
    <div class="abs plan-name">STANDARD PLAN</div>
    <div class="abs plan-price">$89<small>.00</small></div>
    <ul class="abs plan-rows"><li>Responsive</li><li class="off">1.5 GB of storage</li><li>Battery backup 10%</li><li class="off">Smart wallpaper</li><li>50 Feature</li></ul>
    <div class="abs plan-btn">SIGNUP NOW</div>
    <div class="abs plan-foot"></div>
  </div>

  <div class="abs plan" style="left:792px">
    <svg class="abs plan-head" width="317" height="170" viewBox="0 0 317 170"><polygon points="0,0 317,0 317,82 158.5,150 0,82" fill="#33a6d7"/></svg>
    <div class="abs plan-name">BASIC PLAN</div>
    <div class="abs plan-price">$79<small>.00</small></div>
    <ul class="abs plan-rows"><li>Responsive</li><li class="off">1.5 GB of storage</li><li>Battery backup 10%</li><li class="off">Smart wallpaper</li><li>50 Feature</li></ul>
    <div class="abs plan-btn">SIGNUP NOW</div>
    <div class="abs plan-foot"></div>
  </div>
</section>

<section class="reviews">
  <h2 class="abs section-title" style="top:54px;font-weight:700;font-size:24px">CUSTOMER REVIEW</h2>
  <p class="abs review-text">Lorem Ipsum passages, and more recently with desktop publishing software like Orvell PageSetter including versions of Lorem Ipsum Maker including versions</p>
  <svg class="abs" style="left:420px;top:170px" width="360" height="150" viewBox="0 0 360 150">
    <defs>
      <linearGradient id="portraitTone" x1="0" y1="0" x2="0" y2="1">
        <stop offset="0" stop-color="#e9eef1"/>
        <stop offset="0.55" stop-color="#c7b3a3"/>
        <stop offset="1" stop-color="#6f7f8c"/>
      </linearGradient>
    </defs>
    <g role="img" aria-label="Portraits of three customers in hexagon frames">
      <polygon points="42,42 74,42 92,75 74,108 42,108 24,75" fill="url(#portraitTone)" stroke="#fff" stroke-width="4"/>
      <polygon points="318,42 286,42 268,75 286,108 318,108 336,75" fill="url(#portraitTone)" stroke="#fff" stroke-width="4"/>
      <polygon points="140,8 220,8 258,75 220,142 140,142 102,75" fill="url(#portraitTone)" stroke="#fff" stroke-width="5"/>
    </g>
  </svg>
  <svg class="abs" style="left:367px;top:225px" width="14" height="20" viewBox="0 0 14 20"><path d="M11 2L3 10l8 8" fill="none" stroke="#fff" stroke-width="3"/></svg>
  <svg class="abs" style="left:816px;top:225px" width="14" height="20" viewBox="0 0 14 20"><path d="M3 2l8 8-8 8" fill="none" stroke="#fff" stroke-width="3"/></svg>
  <div class="abs review-name">LOREM IPSUM</div>
  <div class="abs review-role">CUSTOMER</div>
</section>

<section class="screens">
  <h2 class="abs section-title display" style="top:48px;font-size:26px">SCREENSHOTS</h2>
  <div class="abs" style="left:0;top:0" role="img" aria-label="Five phones showing screens of the demo shop app">
    <div class="abs handset" style="left:172px;top:185px;width:127px;height:239px"><div class="screen"></div></div>
    <div class="abs handset" style="left:324px;top:149px;width:160px;height:311px"><div class="screen"></div></div>
    <div class="abs handset" style="left:508px;top:125px;width:184px;height:370px"><div class="screen"></div></div>
    <div class="abs handset" style="left:720px;top:149px;width:158px;height:311px"><div class="screen"></div></div>
    <div class="abs handset" style="left:904px;top:185px;width:124px;height:239px"><div class="screen"></div></div>
  </div>
  <svg class="abs" style="left:87px;top:270px" width="14" height="22" viewBox="0 0 14 22"><path d="M11 2L3 11l8 9" fill="none" stroke="#3176b5" stroke-width="3.5"/></svg>
  <svg class="abs" style="left:1098px;top:270px" width="14" height="22" viewBox="0 0 14 22"><path d="M3 2l8 9-8 9" fill="none" stroke="#3176b5" stroke-width="3.5"/></svg>
</section>

<section class="download" role="img" aria-label="Blurred blue photo of a phone on a desk behind the download section">
  <h2 class="abs section-title display">DOWNLOAD APP</h2>
  <p class="abs section-sub">Lorem ipsum dolor sit a met, consectetur adipiscing elit, sed do eiusmod tempor</p>
  <div class="abs store-btn" style="left:274px;width:191px"><div class="mark"></div><span>Available for<b>Nimbus Phone</b></span></div>
  <div class="abs store-btn" style="left:503px;width:194px"><div class="mark"></div><span>Available in<b>Droidly Market</b></span></div>
  <div class="abs store-btn" style="left:732px;width:196px"><div class="mark"></div><span>Available to<b>Download Now</b></span></div>
</section>

<footer class="site-footer">
  <div class="abs footer-brand">Vorbo</div>
  <div class="abs contact-line" style="top:100px">
    <svg width="24" height="20" viewBox="0 0 24 20"><rect width="24" height="20" rx="2" fill="#0355a3"/><path d="M8 5c-1 1-1 3 1.5 6s5 4 6 3l1-1-2-2-1 1c-1 0-3-2-3-3l1-1-2-2z" fill="#fff"/></svg>
    555-014-3902
  </div>
  <div class="abs contact-line" style="top:141px">
    <svg width="24" height="18" viewBox="0 0 24 18"><rect width="24" height="18" rx="2" fill="#0355a3"/><path d="M3 4l9 6 9-6" fill="none" stroke="#fff" stroke-width="1.6"/></svg>
    info.vorbo.example
  </div>
  <div class="abs copyright">@ copyright 2016 Vorbo All Rights Reserved</div>

  <div class="abs pay-badge" role="img" aria-label="Accepted payment methods badge"></div>
  <div class="abs social" style="left:402px"></div>
  <div class="abs social" style="left:440px"></div>
  <div class="abs social" style="left:479px"></div>

  <div class="abs news-title display">Newsletter sign up</div>
  <div class="abs news-note">Enter your email address to receive our newsletter.</div>
  <div class="abs news-form"><div class="field">Email address</div><div class="submit">SUBSCRIBE</div></div>
</footer>

</body>
</html>
```